Calderwell Climate Business Card Design

Design new, 2 sides, business cards for a residential and light commercial heating, air conditioning contractor.

Target Market(s)

Homeowners, small businesses

Industry/Entity Type

Business

Contact Information for Business Card

Dominic Westerhall
Phone - 862-415-2736
Email
Address - PO box 518
Brightwater NJ 07912
Website - www.HarborBreezeLLC.example

Requirements
Must have
• logo, company colors, standard size with no die cut, so I can use nova stamp

```html
<!DOCTYPE html>
<html lang="en">
<head>
<meta charset="utf-8">
<title>Calderwell Climate Business Card</title>
<link rel="stylesheet" href="https://fonts.googleapis.com/css2?family=PT+Sans:ital,wght@0,400;0,700;1,400&display=swap">
<style>
  :root {
    --maroon: #9b1f34;
    --orange: #f48b33;
    --orange-deep: #f39a1e;
    --white: #ffffff;
    --ink: #3b1c1c;
    --backdrop: #d6d6d6;
  }
  * { margin: 0; padding: 0; box-sizing: border-box; }
  html, body { width: 1105px; height: 1200px; overflow: hidden; }
  body {
    background: var(--backdrop);
    font-family: "PT Sans", Arial, sans-serif;
    position: relative;
  }
  .card {
    position: absolute;
    left: 196px;
    width: 720px;
    height: 412px;
    border-radius: 20px;
    overflow: hidden;
    box-shadow: 0 4px 10px rgba(0,0,0,0.25);
  }
  .card--front { top: 146px; background: var(--maroon); }
  .card--back { top: 602px; background: var(--orange); }
  .front-bands { position: absolute; inset: 0; width: 720px; height: 412px; }
  .brand-name {
    position: absolute;
    left: 0; right: 0;
    text-align: center;
    font-weight: 700;
    color: var(--maroon);
    letter-spacing: 1px;
    line-height: 1;
  }
  .card--front .brand-name { top: 92px; font-size: 50px; }
  .card--back .brand-name { top: 160px; font-size: 58px; }
  .contact {
    position: absolute;
    left: 0; right: 0;
    text-align: center;
    color: var(--white);
    font-size: 18px;
    line-height: 1;
  }
  .contact-name { top: 262px; font-size: 23px; }
  .contact-name .person { color: var(--orange); font-weight: 700; text-transform: uppercase; }
  .contact-name .role { font-size: 20px; }
  .contact-phones { top: 302px; }
  .contact-web { top: 331px; }
  .contact-address { top: 358px; }
  .icon { width: 16px; height: 16px; vertical-align: -2px; margin: 0 3px 0 8px; }
  .icon:first-child { margin-left: 0; }
  .tagline {
    position: absolute;
    left: 0; right: 0;
    top: 314px;
    text-align: center;
    font-style: italic;
    font-size: 19px;
    line-height: 25px;
    color: var(--ink);
  }
</style>
</head>
<body>

<section class="card card--front" aria-label="Card front">
  <svg class="front-bands" viewBox="0 0 720 412" aria-hidden="true">
    <path d="M0 120 Q360 346 720 112 L720 0 L0 0 Z" fill="var(--orange-deep)"/>
    <path d="M0 120 Q360 332 720 120 L720 0 L0 0 Z" fill="var(--white)"/>
  </svg>
  <div class="brand-name">Calderwell Climate</div>

  <p class="contact contact-name"><span class="person">Dominic Westerhall /</span> <span class="role">CEO/Founder</span></p>
  <p class="contact contact-phones">
    <svg class="icon" viewBox="0 0 16 16"><path d="M3 1 L6 1 L7 5 L5 6.5 Q6.5 9.5 9.5 11 L11 9 L15 10 L15 13 Q14 15 12 15 Q2 13 1 3 Q1 1 3 1 Z" fill="var(--orange)"/></svg>862 415 2736
    <svg class="icon" viewBox="0 0 16 16"><rect x="4" y="0.5" width="8" height="15" rx="1.5" fill="var(--orange)"/><rect x="5.3" y="2.5" width="5.4" height="9.5" fill="var(--maroon)"/></svg>862 415 2790
    <svg class="icon" viewBox="0 0 16 16"><rect x="4" y="1" width="8" height="5" fill="var(--orange)"/><rect x="1" y="6" width="14" height="7" rx="1.5" fill="var(--orange)"/><rect x="4" y="10" width="8" height="5" fill="var(--orange)" stroke="var(--maroon)" stroke-width="1"/></svg>862 415 2744
  </p>
  <p class="contact contact-web">
    <svg class="icon" viewBox="0 0 16 16"><rect x="1" y="3" width="14" height="10" fill="var(--orange)"/><path d="M1 3 L8 9 L15 3" fill="none" stroke="var(--maroon)" stroke-width="1.3"/></svg>dominic@calderwellclimate.example
    <svg class="icon" viewBox="0 0 16 16"><circle cx="8" cy="8" r="7" fill="var(--orange)"/><path d="M5 4 Q7 6 5 8 Q8 10 7 13 M10 3 Q11 6 13 7" fill="none" stroke="var(--maroon)" stroke-width="1.3"/></svg>www.calderwellclimate.example
  </p>
  <p class="contact contact-address">PO box 518, Brightwater NJ 07912</p>
</section>

<section class="card card--back" aria-label="Card back">
  <div class="brand-name">Calderwell Climate</div>
  <p class="tagline">Residential &amp; light commercial heating<br>Air conditioning contractor</p>
</section>

</body>
</html>
```